Webdesign für Versicherungsmakler
Zielgruppe
Wir sind ein Versicherungsmakler und wollen unseren Internetauftritt modernisieren. Unsere Zielgruppe sind mittelständische Unternehmen. Wir erstellen neben den Sachversicherungen und der Altersvororge auch versicherungsmathematische Gutachten. Wir beraten, erstellen Angebote und verwalten und betreuen die Versicherungsverträge und Schadenfälle unserer Kunden.
Aufgabenstellung
Es besteht bereits eine Website: https://www.k-und-m.de/. An dieser sollte sich orientiert werden, die Inhalte werden vermutlich in Zukunft Ähnlich bleiben.
Der Aufbau der Website soll modernisiert werden. Das Logo soll erhalten bleiben. Die Seite soll einen modernen, cleanen und dennoch zuverlässigen Eindruck vermitteln.

```html
<!DOCTYPE html>
<html lang="de">
<head>
<meta charset="utf-8">
<title>Kettler &amp; Marwede – Versicherungsmakler für Unternehmen</title>
<link href="https://fonts.googleapis.com/css2?family=Nunito+Sans:wght@300;400;600;700;800&display=swap" rel="stylesheet">
<style>
  :root {
    --bg: #f4f3f0;
    --blue: #0a5a98;
    --blue-dark: #0b4f86;
    --coral: #e07a5f;
    --text: #4d4d4d;
    --grey: #5a5a5a;
    --card: #ffffff;
    --line: #e3e3e3;
    --dot: #c9d7e3;
  }
  * { margin: 0; padding: 0; box-sizing: border-box; }
  html, body { width: 1200px; height: 1071px; overflow: hidden; }
  body {
    background: var(--bg);
    font-family: "Nunito Sans", sans-serif;
    color: var(--text);
    position: relative;
  }
  .brand {
    position: absolute; left: 57px; top: 30px;
    display: flex; align-items: center; gap: 10px;
  }
  .brand-mark { width: 14px; height: 14px; background: var(--blue); }
  .brand-name {
    font-size: 22px; font-weight: 400; color: var(--blue);
    letter-spacing: 1.5px; line-height: 1.1; text-transform: uppercase;
  }
  .nav {
    position: absolute; left: 387px; top: 38px;
    display: flex; gap: 32px; font-size: 18px; color: var(--blue);
  }
  .nav .active { color: var(--coral); }
  .btn {
    display: inline-flex; align-items: center; justify-content: center;
    background: var(--blue); color: #fff; font-weight: 600;
    font-size: 15px; letter-spacing: 1px; border-radius: 4px;
  }
  .nav-cta { position: absolute; left: 980px; top: 36px; width: 121px; height: 33px; }
  .hero-title {
    position: absolute; left: 57px; top: 163px;
    color: var(--blue); line-height: 1;
  }
  .hero-title .light { display: block; font-size: 36px; font-weight: 400; }
  .hero-title .bold { display: block; font-size: 40px; font-weight: 800; margin: 12px 0 0 12px; }
  .hero-text {
    position: absolute; left: 66px; top: 263px; width: 410px;
    font-size: 13.5px; line-height: 24.4px; color: var(--grey);
  }
  .hero-cta { position: absolute; left: 66px; top: 401px; width: 121px; height: 33px; }
  .glow {
    position: absolute; left: 700px; top: 100px; width: 480px; height: 400px;
    background: radial-gradient(ellipse at center, rgba(232,160,140,.55) 0%, rgba(240,190,175,.25) 45%, rgba(244,243,240,0) 70%);
  }
  .hero-photo {
    position: absolute; left: 833px; top: 159px; width: 268px; height: 268px;
    border: 4px solid #fff; border-top-left-radius: 46px; overflow: hidden;
    background: linear-gradient(160deg, #c8d9ea 0%, #6d95bf 40%, #2f5f92 70%, #c9d2dc 100%);
  }
  .badge {
    position: absolute; left: 743px; top: 357px; width: 203px; height: 52px;
    background: #fff; border-radius: 4px; box-shadow: 0 2px 8px rgba(0,0,0,.06);
    display: flex; align-items: center; gap: 10px; padding-left: 13px;
  }
  .badge-text {
    color: var(--blue); font-size: 13.5px; font-weight: 600;
    line-height: 18.5px; text-align: center;
  }
  .slider-nav {
    position: absolute; left: 1035px; top: 500px;
    display: flex; align-items: center; gap: 5px;
  }
  .slider-nav .dot { width: 8px; height: 8px; border-radius: 50%; background: var(--dot); }
  .slider-nav .dot.on { background: var(--blue); }
  .welcome {
    position: absolute; left: 0; top: 543px; width: 1165px; text-align: center;
  }
  .welcome h2 { color: var(--blue); font-size: 19px; font-weight: 800; }
  .welcome p {
    position: absolute; left: 0; width: 1200px; top: 40px;
    font-size: 9.5px; line-height: 12.5px; color: var(--grey);
  }
  .cards { position: absolute; left: 129px; top: 637px; display: flex; gap: 19px; }
  .card {
    width: 309px; height: 328px; background: var(--card);
    border: 1px solid var(--line); border-radius: 4px; position: relative;
  }
  .card-art {
    position: absolute; left: 72px; top: 45px; width: 165px; height: 135px;
    border-radius: 10px;
    background: linear-gradient(135deg, #dfe8f0 0%, #c7d7e5 60%, #f1cfc3 100%);
  }
  .card-title {
    position: absolute; top: 228px; left: 0; width: 100%;
    text-align: center; color: var(--blue); font-size: 17px; font-weight: 600; line-height: 23px;
  }
  .card-title.left { text-align: left; padding-left: 50px; }
</style>
</head>
<body>
  <header>
    <div class="brand">
      <span class="brand-mark"></span>
      <span class="brand-name">Kettler<br>&amp; Marwede</span>
    </div>
    <nav class="nav">
      <span class="active">Home</span>
      <span>Profil</span>
      <span>Dienstleistungen</span>
      <span>Unternehmen</span>
      <span>Service</span>
    </nav>
    <span class="btn nav-cta">Kontakt</span>
  </header>

  <section class="hero">
    <h1 class="hero-title">
      <span class="light">Versicherungsmakler</span>
      <span class="bold">für Unternehmen</span>
    </h1>
    <p class="hero-text">is simply dummy text of the printing and typesetting industry. Lorem Ipsum has been the industry’s standard dummy text ever since the 1500s, when an unknown printer took a galley of type and scrambled it to make a type specimen book. It has survived not only five centuries, but also the leap into electronic</p>
    <span class="btn hero-cta">Kontakt</span>

    <div class="glow"></div>
    <div class="hero-photo" role="img" aria-label="Foto eines modernen, geschwungenen Bürohochhauses mit Glasfassade"></div>
    <div class="badge">
      <svg width="26" height="30" viewBox="0 0 26 30" aria-hidden="true">
        <path d="M13 2 L24 6 V14 C24 21 19 26 13 28 C7 26 2 21 2 14 V6 Z" fill="none" stroke="#e07a5f" stroke-width="2"/>
      </svg>
      <div class="badge-text">Versicherungsmakler<br>für Unternehmen</div>
    </div>
    <div class="slider-nav">
      <svg width="14" height="24" viewBox="0 0 14 24" aria-hidden="true"><path d="M11 2 L3 12 L11 22" fill="none" stroke="#0a5a98" stroke-width="3"/></svg>
      <span class="dot on"></span><span class="dot"></span><span class="dot"></span>
      <svg width="14" height="24" viewBox="0 0 14 24" aria-hidden="true"><path d="M3 2 L11 12 L3 22" fill="none" stroke="#0a5a98" stroke-width="3"/></svg>
    </div>
  </section>

  <section class="welcome">
    <h2>Willkommen bei Kettler &amp; Marwede</h2>
    <p>Experten für Ihr Versicherungsmanagement und betriebliche Altersversorgung<br>unabhängiger Versicherungsmakler</p>
  </section>

  <section class="cards">
    <article class="card">
      <div class="card-art" role="img" aria-label="Illustration: Lupe mit Zahnrad, Schutzschild mit Schirm und Kalender"></div>
      <h3 class="card-title">Versicherungsmanagement</h3>
    </article>
    <article class="card">
      <div class="card-art" role="img" aria-label="Illustration: Checkliste mit Schirmsymbol und ältere Person mit Gehstock"></div>
      <h3 class="card-title">Altersvorsorge</h3>
    </article>
    <article class="card">
      <div class="card-art" role="img" aria-label="Illustration: Schutzschild, Karte und steigendes Balkendiagramm mit Pfeil"></div>
      <h3 class="card-title left">Versicherungsmathematische<br>&nbsp;Gutachten</h3>
    </article>
  </section>
</body>
</html>
```